Revamp Of Landing Page For an Automated AI Voice Agents Agency

here is my current landing page https://app.brightfernpromotionhub.biz/v2/preview/WXKRPmQ4hLzYBvNdTeGS?notrack=true

Please use all my current content and imagery of ai agents in your new design. Make it easy to ready, easy to navigate and easy to understand

I am looking for a SLEEK shiny polished looking website. I like Dark themed sites but am open to see light themed sites too so please dont be shy.

The site should have an Ai Voice Agent Theme about it. Maybe look and feel of futureistic but simple and not intimidating to the average person...

Here are a couple website designs I like for reference:
https://q7v.io/
https://ai-bots.marekholvin.com/
https://chatwelmo.com/ai-agents

Target Market(s)

b2b

Industry/Entity Type

AI Voice Agents

Coding

Coded - Design and coding required

Font styles to use
Other font styles liked:
• open

Requirements
Must have
• all elements and content and images used in existing design.
Nice to have
• open
Should not have
• open

```html
<!DOCTYPE html>
<html lang="en">
<head>
<meta charset="utf-8">
<title>Voxaline — Customized AI Agents</title>
<link rel="stylesheet" href="https://fonts.googleapis.com/css2?family=Plus+Jakarta+Sans:wght@300;400;500;600;700;800&display=swap">
<style>
:root{
  --ink:#0f1623;
  --ink-2:#161e2e;
  --purple:#6d3fe2;
  --purple-2:#8a4ff0;
  --text:#111827;
  --muted:#4b5563;
  --line:#e5e7eb;
  --white:#ffffff;
  --star:#f5b301;
}
*{box-sizing:border-box;margin:0;padding:0}
html,body{width:1200px;height:4409px;overflow:hidden}
body{position:relative;font-family:"Plus Jakarta Sans",Arial,sans-serif;color:var(--text);background:var(--white)}
.accent{color:var(--purple);font-weight:700}
.btn{position:absolute;display:flex;align-items:center;justify-content:center;font-size:11px;font-weight:700;letter-spacing:.2px;text-transform:uppercase;border-radius:3px;color:#fff;background:linear-gradient(90deg,var(--purple),var(--purple-2))}
.btn.dark{background:var(--ink-2);border:1px solid #2a3344}

/* hero */
.hero{position:absolute;left:0;top:0;width:1200px;height:705px;background:var(--ink);overflow:hidden}
.logo{position:absolute;display:flex;align-items:center;gap:6px;font-size:18px;font-weight:500;letter-spacing:2px;color:#fff}
.logo i{display:block;width:16px;height:16px;border:2px solid #fff;border-radius:50%}
.nav{position:absolute;left:367px;top:40px;display:flex;gap:16px;font-size:11px;color:#8b93a3;text-transform:uppercase}
.nav .on{color:#fff;text-decoration:underline;font-weight:600}
.hero-title{position:absolute;left:170px;top:176px;font-size:64px;line-height:66px;font-weight:400;color:#fff;letter-spacing:-1.8px}
.hero-lede{position:absolute;left:171px;top:452px;width:440px;font-size:13px;line-height:21px;color:#e5e7eb}
.hero-art{position:absolute;left:625px;top:111px;width:556px;height:594px;background:radial-gradient(ellipse at 45% 45%,#f1f2f5 0%,#bfc3cb 30%,#3a4150 60%,var(--ink) 78%)}
.talk{position:absolute;left:1017px;top:533px;display:flex;align-items:center;gap:8px;color:#fff;font-size:11px;font-weight:700}
.talk i{display:block;width:56px;height:56px;border:3px solid #fff;border-radius:50%}

/* workforce */
.sec-title{position:absolute;left:0;width:1200px;text-align:center;font-size:46px;line-height:50px;font-weight:400;letter-spacing:-1.2px}
.sec-sub{position:absolute;left:0;width:1200px;text-align:center;font-size:13px;line-height:20px}
.row-copy{position:absolute;display:flex;flex-direction:column;align-items:flex-start}
.row-copy.right{left:659px;width:375px}
.row-copy.left{left:171px;width:435px}
.row-label{font-size:11px;line-height:14px;font-weight:700;color:var(--purple);text-transform:uppercase;margin-bottom:8px}
.row-title{width:100%;font-size:26px;line-height:36px;font-weight:600;letter-spacing:-.7px;margin-bottom:16px}
.row-text{width:100%;font-size:11px;line-height:19px;color:var(--muted);margin-bottom:26px}
.row-copy .btn{position:static;width:195px;height:45px}
.portrait{position:absolute;border-radius:50%}
.p-blue{background:radial-gradient(circle at 55% 45%,#e4ecf3 0%,#8ea8bd 45%,#3e5c73 100%)}
.p-teal{background:radial-gradient(circle at 45% 45%,#e7c3a8 0%,#7fa3b1 40%,#1d5b74 100%)}
.p-night{background:radial-gradient(circle at 55% 45%,#b4c6d6 0%,#3c6b8a 45%,#0c2a44 100%)}
.bubble{position:absolute;display:flex;align-items:center;gap:8px;padding:6px 8px;background:#fff;border-radius:3px;box-shadow:0 4px 14px rgba(0,0,0,.12);font-size:10px;line-height:13px;color:#333}
.bubble .av{flex:none;width:30px;height:30px;border-radius:3px;background:#c99a78}
.bubble .bot{flex:none;width:30px;height:30px;border-radius:3px;background:var(--ink)}
.ico{position:absolute;width:72px;height:72px;border-radius:50%;background:#fff;box-shadow:0 4px 14px rgba(0,0,0,.14);display:flex;align-items:center;justify-content:center}
.pill{position:absolute;left:484px;width:127px;height:30px;background:#fff;border-radius:3px;box-shadow:0 3px 10px rgba(0,0,0,.12);display:flex;align-items:center;gap:7px;padding-left:8px;font-size:10px;color:#333}
.pill svg{flex:none}
.meet{position:absolute;left:171px;top:1876px;width:165px;height:96px;background:#fff;border-radius:4px;box-shadow:0 4px 14px rgba(0,0,0,.14);text-align:center;font-size:10px;font-weight:700;padding-top:10px}

/* features */
.band{position:absolute;left:0;top:2520px;width:1200px;height:805px;background:var(--ink);color:#fff;overflow:hidden}
.band .sec-title{color:#fff}
.band .sec-sub{color:#d9dce3}
.feat{position:absolute;width:260px}
.feat h3{font-size:19px;line-height:25px;font-weight:600;letter-spacing:-.4px;margin-bottom:14px}
.feat p{font-size:11px;line-height:19px;color:#d6d9e0}
.vline{position:absolute;width:1px;background:#2b3446}
.hline{position:absolute;height:1px;background:#2b3446}
.wave{position:absolute;left:0;top:613px;width:1200px;height:192px;background:linear-gradient(180deg,rgba(15,22,35,0) 0%,#3a1f7a 40%,#7a3fe0 65%,#3c1a8c 100%)}

/* testimonials */
.t-title{position:absolute;left:170px;top:3378px;font-size:46px;line-height:56px;font-weight:400;letter-spacing:-1.2px}
.arrow{position:absolute;top:3384px;width:44px;height:44px;border-radius:50%;display:flex;align-items:center;justify-content:center}
.card{position:absolute;top:3462px;width:269px;height:202px;border:1px solid var(--line);border-radius:4px;padding:30px 24px}
.card .who{display:flex;align-items:center;gap:12px}
.card .face{width:38px;height:38px;border-radius:50%;background:#9ba5a0}
.card .name{font-size:14px}
.card .date{font-size:10px;color:#555}
.stars{margin:14px 0 10px;color:var(--star);font-size:17px;letter-spacing:2px}
.card p{font-size:11px;line-height:19px;color:#333}

/* cta + footer */
.foot-bg{position:absolute;left:0;top:3852px;width:1200px;height:557px;background:var(--ink)}
.cta{position:absolute;left:171px;top:3727px;width:853px;height:327px;border-radius:10px;background:linear-gradient(120deg,#8f52ef 0%,#6a3fe0 55%,#5b35d6 100%);overflow:hidden;color:#fff;text-align:center}
.cta .kicker{position:absolute;left:0;top:62px;width:100%;font-size:11px;font-weight:700}
.cta h2{position:absolute;left:0;top:82px;width:100%;font-size:46px;line-height:50px;font-weight:400;letter-spacing:-1.2px}
.cta p{position:absolute;left:0;top:191px;width:100%;font-size:13px}
.cta .ring{position:absolute;border:2px solid rgba(255,255,255,.8);border-radius:50%}
.cols{position:absolute;top:4117px;color:#fff}
.cols h4{font-size:11px;font-weight:700;margin-bottom:12px}
.cols li{list-style:none;font-size:12px;line-height:24px;color:#e5e7eb}
.social{position:absolute;top:4147px;left:865px;display:flex;gap:8px}
.social i{display:block;width:34px;height:34px;border:1px solid #fff;border-radius:50%}
.legal{position:absolute;left:0;width:1200px;text-align:center;color:#fff;font-size:11px;line-height:20px}
</style>
</head>
<body>

<header class="hero">
  <div class="logo" style="left:171px;top:38px">VOXALINE <i></i></div>
  <nav class="nav"><span class="on">Home</span><span>About Us</span><span>Testimonials</span><span>Resources</span></nav>
  <div class="btn dark" style="left:762px;top:30px;width:96px;height:37px">Sign In</div>
  <div class="btn" style="left:860px;top:30px;width:165px;height:37px">Build Your AI Chatbot</div>
  <div class="hero-art" role="img" aria-label="White humanoid robot head in profile with glowing ear component"></div>
  <h1 class="hero-title">Creating<br>Customized <span class="accent">AI</span><br><span class="accent">Agent</span> For Your<br>Business.</h1>
  <p class="hero-lede">Simply click the button below and your very own ai agent will be calling you in just a couple minutes. Experience the magic and get ready to be very impressed!</p>
  <div class="btn" style="left:171px;top:539px;width:195px;height:44px">Get An Instant Free Demo</div>
  <div class="btn dark" style="left:375px;top:539px;width:133px;height:44px">Talk To Sales</div>
  <div class="talk"><i></i>TAP TO TALK</div>
</header>

<section class="workforce">
  <h2 class="sec-title" style="top:757px">Meet Your New <span class="accent">AI-Powered</span><br>Business Workforce</h2>
  <p class="sec-sub" style="top:867px">Ai Voice Agents That Answer Calls, Book Appts, Send Emails, Text Messages, Follow<br>Up Reminders, Transfer Calls &amp; More For You 24 Hours 7 Days A Week!</p>

  <!-- sales agent -->
  <div class="portrait p-blue" style="left:257px;top:950px;width:346px;height:342px" role="img" aria-label="Sales agent with headset working at a computer in a city office"></div>
  <div class="bubble" style="left:418px;top:959px;width:193px"><span class="av"></span>Can I change the delivery address for my order?</div>
  <div class="bubble" style="left:171px;top:1113px;width:194px"><span class="bot"></span>Let me check if your order is still eligible for an address change.</div>
  <div class="ico" style="left:527px;top:1198px"><svg width="30" height="30" viewBox="0 0 24 24" fill="none" stroke="#6d3fe2" stroke-width="1.6"><path d="M4 14v-2a8 8 0 0 1 16 0v2"/><rect x="3" y="13" width="4" height="6" rx="2"/><rect x="17" y="13" width="4" height="6" rx="2"/><path d="M19 19c0 2-3 3-6 3"/></svg></div>
  <div class="row-copy right" style="top:973px">
    <div class="row-label">AI Sales Agent</div>
    <h3 class="row-title">Build, scale, and deploy your cloud-native apps and AI agents on one platform</h3>
    <p class="row-text">Brian will take your inbound sales calls. Will give all detailed information to the customer, answer questions in a normal conversational tone and can book the sales appointments or transfer hot prospects to a human to close the sale.</p>
    <div class="btn">Get An Instant Free Demo</div>
  </div>

  <!-- receptionist -->
  <div class="row-copy left" style="top:1372px">
    <div class="row-label">AI Receptionist</div>
    <h3 class="row-title">Takes overflow and after hours calls or can take calls 24/7 and transfer to appropriate dept.</h3>
    <p class="row-text">Cody handles all your calls 24/7. You can also set him to only take overflow calls and after hours. She can send emails and sms messages and even book appointments over the call.</p>
    <div class="btn">Get An Instant Free Demo</div>
  </div>
  <div class="portrait p-teal" style="left:671px;top:1339px;width:344px;height:342px" role="img" aria-label="Smiling receptionist agent wearing a headset"></div>
  <div class="bubble" style="left:661px;top:1346px;width:195px"><span class="av"></span>Can I change the delivery address for my order?</div>
  <div class="bubble" style="left:832px;top:1601px;width:192px"><span class="bot"></span>Let me check if your order is still eligible for an address change.</div>
  <div class="ico" style="left:661px;top:1596px"><svg width="30" height="30" viewBox="0 0 24 24" fill="none" stroke="#6d3fe2" stroke-width="1.6"><circle cx="12" cy="6" r="3"/><path d="M4 14h16l-2 7H6z"/><path d="M9 14v-2h6v2"/></svg></div>

  <!-- appointment setter -->
  <div class="portrait p-night" style="left:260px;top:1726px;width:343px;height:342px" role="img" aria-label="Appointment setter agent with headset typing at a desk"></div>
  <div class="pill" style="top:1736px"><svg width="16" height="16" viewBox="0 0 16 16"><circle cx="8" cy="8" r="8" fill="#6d3fe2"/><path d="M4.5 8.2l2.2 2.2 4.5-4.6" fill="none" stroke="#fff" stroke-width="1.6"/></svg>Your Calender</div>
  <div class="pill" style="top:1775px"><svg width="16" height="16" viewBox="0 0 16 16"><circle cx="8" cy="8" r="8" fill="#6d3fe2"/><path d="M4.5 8.2l2.2 2.2 4.5-4.6" fill="none" stroke="#fff" stroke-width="1.6"/></svg>Custom Assistant</div>
  <div class="pill" style="top:1814px"><svg width="16" height="16" viewBox="0 0 16 16"><circle cx="8" cy="8" r="8" fill="#6d3fe2"/><path d="M4.5 8.2l2.2 2.2 4.5-4.6" fill="none" stroke="#fff" stroke-width="1.6"/></svg>Your Calender</div>
  <div class="meet">
    <svg width="22" height="22" viewBox="0 0 16 16"><circle cx="8" cy="8" r="8" fill="#6d3fe2"/><path d="M4.5 8.2l2.2 2.2 4.5-4.6" fill="none" stroke="#fff" stroke-width="1.6"/></svg>
    <div style="margin-top:4px">MEETING CONFIRMED</div>
    <div style="margin-top:6px;display:flex;justify-content:center;align-items:center;gap:6px;color:#6d3fe2;font-size:9px"><svg width="18" height="18" viewBox="0 0 18 18" fill="none" stroke="#111" stroke-width="1.3"><circle cx="9" cy="9" r="8"/><path d="M9 5v8M5 9h8"/></svg>ADD TO CALENDER</div>
  </div>
  <div class="ico" style="left:527px;top:1979px"><svg width="30" height="30" viewBox="0 0 24 24" fill="none" stroke="#6d3fe2" stroke-width="1.6"><rect x="3" y="5" width="18" height="16" rx="2"/><path d="M3 10h18M8 3v4M16 3v4"/><path d="M9 15l2 2 4-4"/></svg></div>
  <div class="row-copy right" style="top:1780px;width:385px">
    <div class="row-label">AI Appointment Setter</div>
    <h3 class="row-title">Book appts &amp; reservations on auto pilot</h3>
    <p class="row-text" style="width:340px">Bobby offers business advice, helps brainstorm ideas, and provides insights on growth tactics to support your entrepreneurial journey.</p>
    <div class="btn">Get An Instant Free Demo</div>
  </div>

  <!-- lead qualifier -->
  <div class="row-copy left" style="top:2151px">
    <div class="row-label">AI Lead Qualifier</div>
    <h3 class="row-title">Conversate with prospects to qualify before handing over to sales team</h3>
    <p class="row-text">All of our ai agents gather information and qualify leads. If they are interested in the services on the call then our ai agents will assist them with booking an appointment with our sales team over the call.</p>
    <div class="btn">Get An Instant Free Demo</div>
  </div>
  <div class="portrait p-night" style="left:671px;top:2118px;width:344px;height:342px" role="img" aria-label="Lead qualifier agent with headset in a dark tech office"></div>
  <div class="bubble" style="left:661px;top:2123px;width:195px"><span class="av"></span>Can I reschedule my flight to next Monday?</div>
  <div class="bubble" style="left:846px;top:2376px;width:178px"><span class="bot"></span>Your flight has been rescheduled to next Monday.</div>
  <div class="ico" style="left:661px;top:2371px"><svg width="30" height="30" viewBox="0 0 24 24" fill="none" stroke="#6d3fe2" stroke-width="1.6"><circle cx="12" cy="6" r="3"/><path d="M4 14h16l-2 7H6z"/><path d="M9 14v-2h6v2"/></svg></div>
</section>

<section class="band">
  <h2 class="sec-title" style="top:50px">An Employee <span class="accent" style="color:#7c4ff0">That Never</span><br>Gets Sick!</h2>
  <p class="sec-sub" style="top:162px">Your Very Own Ai Agent Will Be Calling You In Just A Couple Minutes. Experience<br>The Magic And Get Ready To Be Very Impressed!</p>

  <div class="vline" style="left:455px;top:240px;height:440px"></div>
  <div class="vline" style="left:770px;top:240px;height:440px"></div>
  <div class="hline" style="left:171px;top:421px;width:853px"></div>

  <div class="feat" style="left:171px;top:240px">
    <svg width="40" height="40" viewBox="0 0 24 24" fill="none" stroke="#7c4ff0" stroke-width="1.5"><circle cx="12" cy="12" r="9"/><path d="M12 7v5l3 3"/></svg>
    <h3 style="margin-top:36px">Trained In Seconds</h3><p>Our AI agent learns Your Entire Website In Seconds.</p></div>
  <div class="feat" style="left:505px;top:240px">
    <svg width="40" height="40" viewBox="0 0 24 24" fill="none" stroke="#7c4ff0" stroke-width="1.5"><circle cx="8" cy="8" r="4"/><circle cx="16" cy="16" r="4"/><path d="M11 11l2 2"/></svg>
    <h3 style="margin-top:12px">Your Wish Is Their Command</h3><p>Your New Ai Agents Will Never Call In Sick And Will Never Complain!</p></div>
  <div class="feat" style="left:801px;top:240px">
    <svg width="40" height="40" viewBox="0 0 24 24" fill="none" stroke="#7c4ff0" stroke-width="1.5"><circle cx="12" cy="12" r="9"/><path d="M3 12h18M12 3c3 3 3 15 0 18M12 3c-3 3-3 15 0 18"/></svg>
    <h3 style="margin-top:36px">Worldwide Available</h3><p>Works Anywhere In The Globe. Boost productivity with AI agents.</p></div>

  <div class="feat" style="left:171px;top:450px">
    <svg width="40" height="40" viewBox="0 0 24 24" fill="none" stroke="#7c4ff0" stroke-width="1.5"><path d="M13 2L4 14h7l-1 8 9-12h-7z"/></svg>
    <h3 style="margin-top:36px">Lightning-Fast Responses</h3><p>Instant answers, no coffee, bathroom or lunch breaks needed</p></div>
  <div class="feat" style="left:505px;top:450px">
    <svg width="40" height="40" viewBox="0 0 24 24" fill="none" stroke="#7c4ff0" stroke-width="1.5"><path d="M12 2v9M14.5 4H11a1.5 1.5 0 0 0 0 3h2a1.5 1.5 0 0 1 0 3H9"/><path d="M3 18l4-3h6l5-2 2 2-7 5H3"/></svg>
    <h3 style="margin-top:12px">14-day Money-back Guarantee</h3><p>It allows customers to receive a full refund for a purchase within 14 days</p></div>
  <div class="feat" style="left:801px;top:450px">
    <svg width="40" height="40" viewBox="0 0 24 24" fill="none" stroke="#7c4ff0" stroke-width="1.5"><circle cx="10" cy="7" r="4"/><path d="M3 21c0-4 3-7 7-7"/><rect x="13" y="15" width="9" height="6" rx="3"/></svg>
    <h3 style="margin-top:36px">User-friendly</h3><p>Your Ai Agents Sound As If They're Real Humans</p></div>

  <div class="wave" role="img" aria-label="Glowing purple particle wave"></div>
</section>

<section class="testimonials">
  <h2 class="t-title">What <span class="accent" style="font-weight:400">Our Clients</span> Are Saying</h2>
  <div class="arrow" style="left:924px;border:1px solid #111"><svg width="18" height="12" viewBox="0 0 18 12" fill="none" stroke="#111" stroke-width="1.5"><path d="M17 6H2M6 1L1 6l5 5"/></svg></div>
  <div class="arrow" style="left:980px;background:#111"><svg width="18" height="12" viewBox="0 0 18 12" fill="none" stroke="#fff" stroke-width="1.5"><path d="M1 6h15M12 1l5 5-5 5"/></svg></div>
  <div class="card" style="left:171px"><div class="who"><span class="face" role="img" aria-label="Reviewer portrait"></span><div><div class="name">Daniel Vorst</div><div class="date">Posted on 16 / 06 / 2024</div></div></div><div class="stars">★★★★★</div><p>After Our Customers Have A Conversation With Their New Ai Voice Agent They Give Us 5 Stars!</p></div>
  <div class="card" style="left:463px"><div class="who"><span class="face" role="img" aria-label="Reviewer portrait"></span><div><div class="name">Daniel Vorst</div><div class="date">Posted on 16 / 06 / 2024</div></div></div><div class="stars">★★★★★</div><p>After Our Customers Have A Conversation With Their New Ai Voice Agent They Give Us 5 Stars!</p></div>
  <div class="card" style="left:755px"><div class="who"><span class="face" role="img" aria-label="Reviewer portrait"></span><div><div class="name">Daniel Vorst</div><div class="date">Posted on 16 / 06 / 2024</div></div></div><div class="stars">★★★★★</div><p>After Our Customers Have A Conversation With Their New Ai Voice Agent They Give Us 5 Stars!</p></div>
</section>

<div class="foot-bg"></div>
<section class="cta">
  <span class="ring" style="left:-120px;top:190px;width:250px;height:250px"></span>
  <span class="ring" style="left:720px;top:-90px;width:220px;height:220px"></span>
  <div class="kicker">INSTALL THE POWER OF AI FOR YOUR BUSINESS</div>
  <h2>Our <b>AI Agents</b> Our Ready<br>To Be Hired</h2>
  <p>These AI Agents Can Help Your Business Tremendously. Imagine The Possibilities</p>
  <div class="btn" style="left:331px;top:235px;width:196px;height:41px;background:var(--ink);border-radius:4px">Get An Instant Free Demo</div>
</section>

<footer>
  <div class="logo" style="left:171px;top:4118px">VOXALINE <i></i></div>
  <div class="cols" style="left:390px"><h4>QUICK LINKS</h4><ul><li>Home</li><li>About us</li><li>Blog</li><li>Testimonials</li><li>Contact</li></ul></div>
  <div class="cols" style="left:522px"><h4>USE CASES</h4><ul><li>Contact centers</li><li>Consumer apps</li><li>Learning &amp; development</li><li>AI dubbing</li><li>AI voice cloning</li></ul></div>
  <div class="cols" style="left:702px"><h4>INDUSTRY</h4><ul><li>Automotive</li><li>Banking</li><li>Consumer Good</li><li>Energy</li><li>Government</li></ul></div>
  <div class="cols" style="left:865px"><h4>STAY SOCIAL</h4></div>
  <div class="social"><i></i><i></i><i></i><i></i></div>
  <p class="legal" style="top:4304px">© 2025 Voxaline | Privacy | Terms &amp; Conditions | Earnings &amp; Products Disclaimer</p>
  <p class="legal" style="top:4336px">IMPORTANT: This site is not a part of the Friendlink website or Friendlink Inc. Additionally, this site is NOT endorsed by Friendlink<br>in any way. FRIENDLINK is a trademark of FRIENDLINK, Inc.</p>
</footer>

</body>
</html>
```